We need UI/UX design for a public, informational website for The Copper Lantern.
The pages, structure, and content scope are already defined. Designers are required to work only on the UI/UX layout of these existing pages, focusing on clarity, hierarchy, spacing, and usability. Do not add, remove, rename, or reinterpret pages or content.
The website is strictly informational only. It must not include accounts, onboarding, payments, custody, escrow administration, marketplaces, dashboards, or any transactional functionality.
Scope of work
Apply UI/UX design to the predefined website pages
Design layout for text, images, notices, and sections
Ensure consistent components and layout patterns across page types
Optimize layouts for long form, compliance focused content
Content writing, page creation, and branding changes are out of scope.
Structure reference
The complete page list, hierarchy, and content definitions are provided in the technical documentation and must be treated as the primary source of truth.
A Figma link is provided only as a light visual reference for page existence and structure:
https://meadow-knot-48203956.plumsite.example/
Designers must rely on the documentation for in depth and authoritative reference.
Brand guidelines
The Copper Lantern has existing brand guidelines and official logos, including light and dark versions. These assets will be provided and must be followed exactly. Designers must not redesign, alter, or reinterpret the brand identity.
Look and feel direction
The desired visual direction is inspired by:
https://ledgerwaltz.example/
This reference is provided only to indicate:
Institutional and enterprise tone
Clean, modern typography
Strong hierarchy and generous whitespace
Editorial, content first layouts
Do not copy branding, layouts, components, or assets from the reference site.
Hero section direction
The hero section should follow a similar structural approach to the hero used on https://ledgerwaltz.example/
, meaning:
Strong editorial framing
Clear headline hierarchy
Calm, institutional first impression
However, the background video must be Abu Dhabi focused, not generic or global. The video should visually reflect:
Abu Dhabi skyline or architectural language
Institutional, sovereign, long term infrastructure tone
Clean, slow, cinematic motion
No promotional, marketing, or lifestyle visuals
The hero must remain informational, restrained, and credible. No hype. No calls to invest. No implied participation.
Constraints
One global primary CTA only: “Continue to Halvemark” (external)
All other interactions must be informational
No visuals or language implying offers, investment, eligibility, or participation
Clear separation between informational content and any external operational platforms
Deliverables
High fidelity UI/UX designs created in Figma, covering:
Desktop layouts
Tablet layouts where relevant
Mobile layouts
Complete Figma file(s) including:
All designed pages defined in the technical documentation
A reusable component library (headers, footers, cards, notice panels, forms, CTAs, typography styles, spacing system)
Clearly defined layout grids, spacing rules, and text styles
Proper use of components and variants, not detached frames
Designs prepared for developer handoff, including:
Clear layer naming and structure
Auto layout where appropriate
Consistent use of styles and components
Responsive behavior demonstrated within Figma
Notes or annotations only where necessary for clarity
No prototypes, interactions, or motion design beyond basic layout states, unless explicitly requested. The focus is static UI/UX clarity, not animation.
A detailed technical specification document and official brand assets will be provided.
Any designs delivered outside Figma, that alter structure or content, or that ignore the defined constraints, boundaries, or tone will be rejected.

```html
<!DOCTYPE html>
<html lang="en">
<head>
<meta charset="utf-8">
<title>The Copper Lantern — Governance Framework</title>
<link href="https://fonts.googleapis.com/css2?family=Sora:wght@300;400;500;600&family=Inter:wght@400;500;600&display=swap" rel="stylesheet">
<style>
:root{
  --stage:#b4b4b4;
  --ink:#0b0b0f;
  --black:#000;
  --white:#fff;
  --mist:#f1f4f9;
  --muted:#5c6270;
  --line:#d9dde5;
  --accent:#3d9bff;
  --cyan:#22d6ff;
  --violet:#a87cff;
  --navy:#1b2848;
  --navy-deep:#0d1426;
}
*{box-sizing:border-box;margin:0;padding:0}
html,body{width:1200px;height:4264px;overflow:hidden}
body{background:var(--stage);font-family:"Inter",sans-serif;color:var(--ink)}
.page{position:absolute;left:81px;top:81px;width:1038px;height:4102px;background:var(--mist);overflow:hidden;box-shadow:0 4px 18px rgba(0,0,0,.25)}
.abs{position:absolute}
h1,h2,h3,h4{font-family:"Sora",sans-serif;font-weight:400}
.center{text-align:center;left:0;right:0}

/* hero */
.hero{position:absolute;left:0;top:0;width:1038px;height:640px}
.brand{position:absolute;left:13px;top:10px;display:flex;align-items:center;gap:8px;color:var(--white);font-family:"Sora",sans-serif;font-size:12px;letter-spacing:.04em}
.brand-dot{width:34px;height:34px;border:1.5px solid var(--white);border-radius:50%}
.nav{position:absolute;top:16px;left:0;right:0;display:flex;justify-content:center;gap:26px;font-size:9.5px;color:var(--white)}
.nav a{color:inherit;text-decoration:none}
.nav .active{color:var(--accent);border-bottom:1px solid var(--accent);padding-bottom:2px}
.cta-top{position:absolute;left:919px;top:10px;width:105px;height:20px;border-radius:10px;background:var(--white);color:var(--ink);font-size:8.5px;display:flex;align-items:center;justify-content:center;font-weight:500}
.hero-title{position:absolute;top:342px;left:0;right:0;text-align:center;color:var(--white);font-size:35px;line-height:45px;font-weight:400;letter-spacing:-.01em}
.hero-sub{position:absolute;top:445px;left:0;right:0;text-align:center;color:#d8def0;font-size:16px;line-height:27px;font-weight:300;font-family:"Sora",sans-serif}
.hero-btn{position:absolute;left:447px;top:510px;width:142px;height:25px;border:1px solid var(--cyan);border-radius:13px;color:var(--white);font-size:10.5px;display:flex;align-items:center;justify-content:center}

/* labels */
.eyebrow{font-size:9.5px;color:var(--accent);font-weight:500}
.body-sm{font-size:8.5px;line-height:13px;color:#333}

/* backers */
.backers{top:708px;font-size:10px;color:var(--accent);letter-spacing:.03em}
.backer{position:absolute;top:745px;width:70px;height:60px;display:flex;flex-direction:column;align-items:center;gap:9px}
.backer-mark{width:30px;height:30px;border:2px solid #222;border-radius:4px}
.backer-name{font-family:"Sora",sans-serif;font-size:8px;letter-spacing:.12em;color:#222}

/* about */
.about-title{left:147px;top:915px;font-size:27px;line-height:32px;width:380px}
.about-copy{left:147px;top:1015px;width:355px}
.pill-dark{position:absolute;height:24px;border-radius:12px;background:var(--black);color:var(--white);font-size:10px;display:flex;align-items:center;justify-content:center}
.tile{position:absolute;top:895px;width:113px;height:214px;border-radius:2px}
.tile-label{position:absolute;left:13px;bottom:18px;color:var(--white);font-size:10px;line-height:12px}
.tile-icon{width:22px;height:22px;border:1px solid rgba(255,255,255,.7);border-radius:3px;margin-bottom:6px}

/* role cards */
.section-title{font-size:28px;line-height:34px}
.role-card{position:absolute;top:1258px;width:230px;height:330px;background:var(--white)}
.role-photo{height:141px}
.icon-box{position:absolute;width:38px;height:38px;background:var(--white);border:1.5px solid transparent;border-radius:3px;background:linear-gradient(var(--white),var(--white)) padding-box,linear-gradient(135deg,var(--cyan),var(--violet)) border-box;display:flex;align-items:center;justify-content:center}
.role-card .icon-box{left:18px;top:121px}
.role-card h3{position:absolute;left:18px;top:176px;font-size:17px}
.role-card .body-sm{position:absolute;left:18px;top:203px;width:195px;font-size:8px;line-height:12px;color:#555}
.meta{position:absolute;left:18px;width:195px;display:flex;font-size:8px;border-bottom:1px solid #eee;padding-bottom:5px}
.meta span:first-child{width:60px;color:#777}
.meta span:last-child{font-weight:600}

/* framework */
.framework{position:absolute;left:0;top:1668px;width:1038px;height:634px;background:var(--black);color:var(--white)}
.fw-item{position:absolute;left:467px;width:422px;border-bottom:1px solid #333;padding-bottom:12px}
.fw-num{font-size:8px;color:#aaa}
.fw-item h4{font-size:16px;margin:8px 0 5px}
.fw-item p{font-size:8px;line-height:13px;color:#aaa}

/* reviewers */
.reviewers{position:absolute;left:0;top:2627px;width:1038px;height:398px;background:var(--white)}
.rev-card{position:absolute;top:126px;width:170px;height:195px;background:var(--mist);padding:22px 20px}
.rev-card .icon-box{position:static;width:42px;height:42px;margin-bottom:18px}
.rev-card h4{font-size:12.5px;line-height:16px;margin-bottom:8px}
.rev-card p{font-size:8px;line-height:12.5px;color:#555}

/* why */
.why-item{position:absolute;width:340px;text-align:center}
.why-item .icon-box{position:static;margin:0 auto 20px;width:42px;height:42px}
.why-item h4{font-size:12.5px;margin-bottom:8px}
.why-item p{font-size:8px;line-height:13px;color:#555}

/* closing cards */
.close-card{position:absolute;top:3588px;width:361px;height:200px;border-radius:10px;text-align:center;padding-top:27px}
.close-card .eyebrow{font-size:8.5px;text-transform:uppercase}
.close-card h2{font-size:24px;line-height:30px;margin:10px 0 8px}
.close-card p{font-size:10px;line-height:16px;padding:0 40px}
.close-btn{display:inline-flex;margin-top:13px;height:25px;padding:0 16px;border-radius:13px;font-size:10px;align-items:center}

/* footer */
.footer{position:absolute;left:0;top:3866px;width:1038px;height:236px;background:var(--black);color:var(--white)}
.foot-col{position:absolute;top:28px;font-size:7.5px;line-height:15.5px;color:#cfcfcf}
.foot-col h5{font-size:8.5px;font-weight:500;color:var(--white);margin-bottom:4px}
.foot-legal{position:absolute;left:190px;top:176px;width:740px;font-size:7px;line-height:12px;color:#aaa}
</style>
</head>
<body>
<main class="page">

  <!-- Hero -->
  <header class="hero">
    <svg width="1038" height="640" viewBox="0 0 1038 640" role="img" aria-label="Abu Dhabi skyline at dusk in deep navy tones">
      <defs>
        <linearGradient id="heroSky" x1="0" y1="0" x2="0" y2="1">
          <stop offset="0" stop-color="#1d2d4a"/>
          <stop offset=".45" stop-color="#243556"/>
          <stop offset=".8" stop-color="#2f2f6e"/>
          <stop offset="1" stop-color="#3b3690"/>
        </linearGradient>
        <linearGradient id="heroEdge" x1="0" x2="1">
          <stop offset="0" stop-color="#2f8bff"/>
          <stop offset=".5" stop-color="#3a6cff"/>
          <stop offset="1" stop-color="#b58cff"/>
        </linearGradient>
      </defs>
      <path d="M0 0H1038V523Q519 705 0 523Z" fill="url(#heroSky)"/>
      <path d="M0 523Q519 705 1038 523" fill="none" stroke="url(#heroEdge)" stroke-width="6"/>
      <circle cx="518" cy="624" r="12" fill="#6cb6ff"/>
      <path d="M512 621L518 629L524 621" fill="none" stroke="#fff" stroke-width="1.5"/>
    </svg>
    <div class="brand"><span class="brand-dot"></span>The Copper Lantern</div>
    <nav class="nav">
      <a class="active">Home</a><a>Framework</a><a>Projects</a><a>Company</a><a>Insights</a><a>Contact</a>
    </nav>
    <a class="cta-top">Continue to Halvemark</a>
    <h1 class="hero-title">A Governance Framework for<br>Structured Project Oversight</h1>
    <p class="hero-sub">Clear boundaries. Institutional discipline. Transparent<br>structures for managing risk and accountability.</p>
    <a class="hero-btn">Learn the Framework</a>
  </header>

  <!-- Backers -->
  <p class="abs center backers">Backed By Leading Institutions And Individuals</p>
  <div class="backer" style="left:112px"><span class="backer-mark"></span><span class="backer-name">COMPANY</span></div>
  <div class="backer" style="left:250px"><span class="backer-mark" style="border-radius:50%"></span><span class="backer-name">COMPANY</span></div>
  <div class="backer" style="left:385px"><span class="backer-mark"></span><span class="backer-name">COMPANY</span></div>
  <div class="backer" style="left:522px"><span class="backer-mark" style="border-radius:50%"></span><span class="backer-name">COMPANY</span></div>
  <div class="backer" style="left:657px"><span class="backer-mark"></span><span class="backer-name">COMPANY</span></div>
  <div class="backer" style="left:794px"><span class="backer-mark" style="border-radius:50%"></span><span class="backer-name">COMPANY</span></div>

  <!-- About -->
  <p class="abs eyebrow" style="left:147px;top:896px;font-size:8.5px">About The Copper Lantern</p>
  <h2 class="abs about-title">From Governance Frameworks to Intelligent Infrastructure</h2>
  <p class="abs body-sm about-copy">The Copper Lantern is a governance and project origination group focused on defining structural standards for complex initiatives. We publish clear frameworks that explain role separation, accountability, and long-term oversight across governance, operations, and project-level execution.</p>
  <a class="pill-dark" style="left:147px;top:1084px;width:114px">Our Framework</a>

  <div class="tile" style="left:538px;background:linear-gradient(160deg,#25344f,#3a3d6e 70%,#2b2150)" role="img" aria-label="Business professionals in dark suits">
    <div class="tile-label"><div class="tile-icon"></div>Clear Role<br>Separation</div></div>
  <div class="tile" style="left:657px;background:linear-gradient(160deg,#1f3140,#2f4a55 60%,#2b2150)" role="img" aria-label="Hands arranging network figures">
    <div class="tile-label"><div class="tile-icon"></div>Independent<br>Oversight<br>Principles</div></div>
  <div class="tile" style="left:776px;background:linear-gradient(160deg,#243a52,#2f4d6e 60%,#2b2150)" role="img" aria-label="Professional touching a digital quality badge">
    <div class="tile-label"><div class="tile-icon"></div>Institutional-Grade<br>Standards</div></div>

  <!-- Understanding our role -->
  <p class="abs center eyebrow" style="top:1192px;font-size:8.5px">Role Clarity</p>
  <h2 class="abs center section-title" style="top:1210px">Understanding Our Role</h2>

  <article class="role-card" style="left:147px">
    <div class="role-photo" style="background:linear-gradient(135deg,#0f2550,#1f4c9a 55%,#0c1a38)" role="img" aria-label="Businessman with digital governance icons"></div>
    <div class="icon-box"><svg width="20" height="20" viewBox="0 0 20 20" fill="none" stroke="#5a7cff" stroke-width="1.3"><path d="M3 8L10 3L17 8M5 9V15M10 9V15M15 9V15M3 17H17"/></svg></div>
    <h3>Governance</h3>
    <p class="body-sm">We define structural frameworks, role boundaries, and oversight mechanisms. This is our domain.</p>
    <div class="meta" style="top:252px"><span>Category</span><span>Governance Framework</span></div>
    <div class="meta" style="top:276px"><span>Audience</span><span>Institutional &amp; Public Reference</span></div>
    <div class="meta" style="top:300px;border:0"><span>Disclosure</span><span>Informational Use Only *</span></div>
  </article>
  <article class="role-card" style="left:403px">
    <div class="role-photo" style="background:linear-gradient(135deg,#0e3a3e,#1f6b70 55%,#0d2228)" role="img" aria-label="Hand touching digital operations icons"></div>
    <div class="icon-box"><svg width="20" height="20" viewBox="0 0 20 20" fill="none" stroke="#5a7cff" stroke-width="1.3"><circle cx="10" cy="10" r="3"/><circle cx="10" cy="10" r="7" stroke-dasharray="3 2"/></svg></div>
    <h3>Operations</h3>
    <p class="body-sm">Day-to-day execution and project management occur outside our organization, through Halvemark.</p>
    <div class="meta" style="top:252px"><span>Category</span><span>Governance Framework</span></div>
    <div class="meta" style="top:276px"><span>Audience</span><span>Institutional &amp; Public Reference</span></div>
    <div class="meta" style="top:300px;border:0"><span>Disclosure</span><span>Informational Use Only *</span></div>
  </article>
  <article class="role-card" style="left:659px">
    <div class="role-photo" style="background:linear-gradient(135deg,#2a3440,#5a6370 55%,#1c222c)" role="img" aria-label="Hands typing on a laptop with transaction icons"></div>
    <div class="icon-box"><svg width="20" height="20" viewBox="0 0 20 20" fill="none" stroke="#5a7cff" stroke-width="1.3"><rect x="4" y="3" width="12" height="14" rx="1"/><path d="M7 7H13M7 10H13M7 13H11"/></svg></div>
    <h3>Transactions</h3>
    <p class="body-sm">We do not facilitate, execute, or participate in any financial transactions or operational activities.</p>
    <div class="meta" style="top:252px"><span>Category</span><span>Governance Framework</span></div>
    <div class="meta" style="top:276px"><span>Audience</span><span>Institutional &amp; Public Reference</span></div>
    <div class="meta" style="top:300px;border:0"><span>Disclosure</span><span>Informational Use Only *</span></div>
  </article>

  <!-- Framework -->
  <section class="framework">
    <p class="abs eyebrow" style="left:147px;top:76px;font-size:8.5px">Core Governance Principles</p>
    <h2 class="abs" style="left:147px;top:100px;font-size:27px">The Framework</h2>
    <p class="abs" style="left:147px;top:147px;width:230px;font-size:8.5px;line-height:14px;color:#ddd">A structured set of principles defining oversight, accountability, and role separation.</p>

    <div class="fw-item" style="top:80px"><div class="fw-num">01</div><h4>Role Boundaries</h4><p>Clear separation between governance responsibilities, operational platforms, and project-level execution to prevent overlap and ambiguity.</p></div>
    <div class="fw-item" style="top:180px"><div class="fw-num">02</div><h4>SPV Structure</h4><p>Ring-fenced project structures designed to isolate liability, clarify accountability, and support disciplined execution.</p></div>
    <div class="fw-item" style="top:280px"><div class="fw-num">03</div><h4>Escrow Model</h4><p>Independent escrow principles describing conditional release mechanisms and third-party oversight—without operational execution on this site.</p></div>
    <div class="fw-item" style="top:380px"><div class="fw-num">04</div><h4>Records and Registers</h4><p>Standards for documentation, evidence records, and transparency to support auditability and structural clarity.</p></div>
    <div class="fw-item" style="top:480px"><div class="fw-num">05</div><h4>Risk and Boundaries</h4><p>Defined limitation frameworks outlining scope, risk containment, and enforcement of governance boundaries.</p></div>
  </section>

  <div class="abs" style="left:0;top:2302px;width:1038px;height:325px;background:linear-gradient(120deg,#6e6a5e,#b5a88a 35%,#8f8a7c 55%,#c9b890 75%,#5d5a52)" role="img" aria-label="Aerial view of a waterfront marina between high-rise towers"></div>

  <!-- Reviewers -->
  <section class="reviewers">
    <h2 class="abs center section-title" style="top:76px">For Framework Reviewers</h2>
    <div class="rev-card" style="left:147px">
      <div class="icon-box"><svg width="22" height="22" viewBox="0 0 22 22" fill="none" stroke="#5a7cff" stroke-width="1.3"><rect x="4" y="3" width="11" height="15"/><circle cx="15" cy="15" r="3"/><path d="M17 17L20 20"/></svg></div>
      <h4>Review Governance Structures</h4><p>Explore published frameworks outlining governance models, role separation, and accountability principles.</p></div>
    <div class="rev-card" style="left:339px">
      <div class="icon-box"><svg width="22" height="22" viewBox="0 0 22 22" fill="none" stroke="#5a7cff" stroke-width="1.3"><rect x="4" y="4" width="14" height="14"/><path d="M7 11L10 14L16 8"/></svg></div>
      <h4>Defined Structural Ownership</h4><p>Frameworks clarify responsibility and authority boundaries without operational or transactional execution.</p></div>
    <div class="rev-card" style="left:530px">
      <div class="icon-box"><svg width="22" height="22" viewBox="0 0 22 22" fill="none" stroke="#5a7cff" stroke-width="1.3"><rect x="3" y="5" width="16" height="12"/><circle cx="11" cy="11" r="3"/></svg></div>
      <h4>Operational Independence</h4><p>Execution, asset handling, and platform operations occur outside this site through independent entities.</p></div>
    <div class="rev-card" style="left:720px">
      <div class="icon-box"><svg width="22" height="22" viewBox="0 0 22 22" fill="none" stroke="#5a7cff" stroke-width="1.3"><rect x="5" y="10" width="12" height="9"/><path d="M8 10V7A3 3 0 0 1 14 7V10"/></svg></div>
      <h4>Clear Access Boundaries</h4><p>This site provides documentation and reference materials only—no onboarding, custody, or execution.</p></div>
  </section>

  <!-- Why -->
  <h2 class="abs center section-title" style="top:3098px">Why The Copper Lantern</h2>
  <div class="why-item" style="left:158px;top:3155px">
    <div class="icon-box"><svg width="22" height="22" viewBox="0 0 22 22" fill="none" stroke="#5a7cff" stroke-width="1.3"><path d="M11 3L18 6V11C18 15 15 18 11 19C7 18 4 15 4 11V6Z"/><path d="M8 11L10 13L14 9"/></svg></div>
    <h4>Governance-First Approach</h4><p>We prioritize structural clarity and accountability, treating governance as the foundation—not an afterthought.</p></div>
  <div class="why-item" style="left:539px;top:3155px">
    <div class="icon-box"><svg width="22" height="22" viewBox="0 0 22 22" fill="none" stroke="#5a7cff" stroke-width="1.3"><rect x="4" y="3" width="14" height="16"/><path d="M7 8H15M7 11H15M7 14H12"/></svg></div>
    <h4>Proven Structural Principles</h4><p>Our frameworks are informed by institutional standards across governance, compliance, and long-term infrastructure design.</p></div>
  <div class="why-item" style="left:158px;top:3299px">
    <div class="icon-box"><svg width="22" height="22" viewBox="0 0 22 22" fill="none" stroke="#5a7cff" stroke-width="1.3"><circle cx="11" cy="6" r="2.5"/><circle cx="5" cy="16" r="2.5"/><circle cx="17" cy="16" r="2.5"/><path d="M11 9V12M7 14L11 12L15 14"/></svg></div>
    <h4>Bridging Structure &amp; Execution</h4><p>We define governance and role boundaries while execution occurs independently through separate operational platforms.</p></div>
  <div class="why-item" style="left:539px;top:3299px">
    <div class="icon-box"><svg width="22" height="22" viewBox="0 0 22 22" fill="none" stroke="#5a7cff" stroke-width="1.3"><rect x="4" y="3" width="12" height="15"/><circle cx="15" cy="15" r="3"/><path d="M17 17L20 20"/></svg></div>
    <h4>Defined Control &amp; Boundaries</h4><p>Clear limitations ensure responsibilities remain properly scoped, auditable, and enforceable.</p></div>

  <!-- Closing band -->
  <svg class="abs" style="left:0;top:3440px" width="1038" height="426" viewBox="0 0 1038 426">
    <defs>
      <linearGradient id="bandFill" x1="0" x2="1">
        <stop offset="0" stop-color="#1ed8ff"/>
        <stop offset=".5" stop-color="#4a9dff"/>
        <stop offset="1" stop-color="#a97cff"/>
      </linearGradient>
    </defs>
    <path d="M0 133Q519 -91 1038 133V426H0Z" fill="url(#bandFill)"/>
    <path d="M0 133Q519 -91 1038 133" fill="none" stroke="#000" stroke-width="6"/>
    <circle cx="518" cy="34" r="11" fill="#000"/>
    <path d="M513 37L518 30L523 37Z" fill="none" stroke="#fff" stroke-width="1.3"/>
  </svg>

  <div class="close-card" style="left:147px;background:var(--white)">
    <p class="eyebrow">For Project Originators</p>
    <h2>Define Your Project’s<br>Governance Framework</h2>
    <p style="color:#444">Design clear structural roles, accountability boundaries, and oversight principles before operational execution begins.</p>
    <a class="close-btn" style="background:var(--black);color:var(--white)">Start a Framework Discussion</a>
  </div>
  <div class="close-card" style="left:530px;background:var(--black);color:var(--white)">
    <p class="eyebrow">For Research &amp; Review</p>
    <h2>Explore Governance<br>Frameworks</h2>
    <p style="color:#ccc">Review published structures outlining role separation, risk boundaries, and long-term oversight models.</p>
    <a class="close-btn" style="background:var(--white);color:var(--ink)">View Frameworks</a>
  </div>

  <!-- Footer -->
  <footer class="footer">
    <div class="foot-col" style="left:190px;width:150px"><h5>The Copper Lantern</h5>A governance framework for structured project oversight and risk management.</div>
    <div class="foot-col" style="left:359px"><h5>Framework</h5>Role Boundaries<br>SPV Structure<br>Escrow Model<br>Records and Registers<br>Risk and Boundaries</div>
    <div class="foot-col" style="left:528px"><h5>Company</h5>About<br>Leadership<br>Governance<br>Press<br>Careers<br>Contact</div>
    <div class="foot-col" style="left:697px"><h5>Legal</h5>Terms of Use<br>Privacy Policy<br>Cookie Policy<br>Disclaimer and Risk Notices<br>Acceptable Use<br>Accessibility</div>
    <p class="foot-legal">© 2026 The Copper Lantern. All rights reserved.<br><br>This website provides informational content only. The Copper Lantern does not provide investment advice, execute projects, or facilitate transactions. All operational activities are conducted through Halvemark, a separate platform.</p>
  </footer>

</main>
</body>
</html>
```